REEF HARVEST

I need to design business cards, and logo for letterhead. It’s a import business for Kava

Target Market(s)

Island food stores, individuals,herbal stores

Industry/Entity Type

Import

Contact Information for Business Card

Mark Dunleigh, 0471526093 address:7 Banfield Close, Corbett Heights,NSW

Font styles to use
Decorative

Colors
FFC000
F8CF3A
FAE287
FDF2CF
FEFAEE

Requirements
Must have
• Logo, picture kava plant, possibly a world map or a plane symbolises importing
Nice to have
• Eye catching logo and a slogan

```html
<!DOCTYPE html>
<html lang="en">
<head>
<meta charset="utf-8">
<title>Reef Harvest – Business Card</title>
<link rel="stylesheet" href="https://fonts.googleapis.com/css2?family=Lato:wght@700&family=Arimo:wght@400&display=swap">
<style>
  :root {
    --canvas-bg: #e9e7e5;
    --card-bg: #f6f2f1;
    --card-black: #000000;
    --brand-yellow: #ffc000;
    --text-light: #f2f2f2;
  }
  * { margin: 0; padding: 0; box-sizing: border-box; }
  html, body {
    width: 1200px;
    height: 900px;
    overflow: hidden;
    background: var(--canvas-bg);
  }
  .business-card {
    position: absolute;
    left: 100px;
    top: 141px;
    width: 1000px;
    height: 618px;
    background: var(--card-bg);
    overflow: hidden;
    box-shadow: 0 10px 30px rgba(0,0,0,0.15);
  }
  .card-shapes {
    position: absolute;
    inset: 0;
    width: 100%;
    height: 100%;
  }
  .brand-mark {
    position: absolute;
    left: 72px;
    top: 198px;
    display: flex;
    align-items: center;
    gap: 16px;
  }
  .brand-dot {
    width: 40px;
    height: 40px;
    border-radius: 50%;
    background: var(--brand-yellow);
  }
  .brand-name {
    font-family: "Lato", sans-serif;
    font-weight: 700;
    font-size: 42px;
    letter-spacing: 1px;
    color: var(--brand-yellow);
    line-height: 1;
  }
  .contact-block {
    position: absolute;
    right: 50px;
    top: 325px;
    text-align: right;
  }
  .contact-name {
    font-family: "Lato", sans-serif;
    font-weight: 700;
    font-size: 40px;
    color: var(--brand-yellow);
    line-height: 1;
    margin-bottom: 16px;
  }
  .contact-row {
    display: flex;
    justify-content: flex-end;
    align-items: center;
    gap: 10px;
    font-family: "Arimo", sans-serif;
    font-size: 27px;
    color: var(--text-light);
    line-height: 1.25;
  }
  .contact-row--address { margin-top: 44px; align-items: flex-start; }
  .contact-icon { width: 42px; height: 42px; flex: none; }
</style>
</head>
<body>
  <div class="business-card">
    <svg class="card-shapes" viewBox="0 0 1000 618" preserveAspectRatio="none" aria-hidden="true">
      <!-- yellow swoosh -->
      <path fill="var(--brand-yellow)"
        d="M0,372 C60,410 150,445 240,440 C380,432 470,330 556,243 C480,320 390,410 250,458 C150,478 60,445 0,420 Z"/>
      <!-- thin black swoosh -->
      <path fill="var(--card-black)"
        d="M260,490 C420,450 560,240 760,170 C800,160 830,162 833,165 C700,165 560,300 460,400 C400,450 330,485 260,490 Z"/>
      <!-- main black field -->
      <path fill="var(--card-black)"
        d="M0,413 C110,470 210,492 300,472 C450,432 600,205 800,185 C880,178 950,200 1000,225 L1000,618 L0,618 Z"/>
    </svg>

    <div class="brand-mark">
      <span class="brand-dot"></span>
      <span class="brand-name">REEF HARVEST</span>
    </div>

    <div class="contact-block">
      <p class="contact-name">MARK DUNLEIGH</p>
      <p class="contact-row">
        <span>0471526093</span>
        <svg class="contact-icon" viewBox="0 0 42 42" aria-hidden="true">
          <circle cx="21" cy="21" r="19" fill="none" stroke="var(--brand-yellow)" stroke-width="2.5"/>
          <path fill="var(--brand-yellow)" d="M14,12 l4,-1 l3,6 l-2.5,2 c1,3 3,5 6,6 l2,-2.5 l6,3 l-1,4 c-9,1 -18,-8 -17.5,-17.5 Z"/>
        </svg>
      </p>
      <p class="contact-row contact-row--address">
        <span>7 Banfield Close<br>Corbett Heights,NSW</span>
        <svg class="contact-icon" viewBox="0 0 42 42" aria-hidden="true">
          <circle cx="21" cy="21" r="19" fill="none" stroke="var(--brand-yellow)" stroke-width="2.5"/>
          <path fill="var(--brand-yellow)" d="M21,9 c-5,0 -8,3.5 -8,8 c0,5.5 8,14 8,14 c0,0 8,-8.5 8,-14 c0,-4.5 -3,-8 -8,-8 Z"/>
          <circle cx="21" cy="17" r="3" fill="var(--card-black)"/>
        </svg>
      </p>
    </div>
  </div>
</body>
</html>
```